1 Dimensional cover for digital product

Please note that if a designer comes in with an original design and other designers try to copy them too closely I will always work with the original designer in order to get the actual look I want.
Therefore it is in the interests of the designers to get their concepts in first.

I am designing some audio products for football (soccer players).

I would like a square version and a 16:9 version of the packaging completed. The square version will be for the Sonvia audio cover and the 16:9 for the thumbnails of videos.

I would like the final images in PSP files as a template that I can change the title and the main image.

I am open to creativity in this project but would like it to be a luxury and premium in what it is portraying.

I have added my logo and also the packaging that I currently use on my sister website which is not aimed at football, soccer.

I've also included an image of one of my models. This would NOT be the product image, but it could be a background image, or you may choose to leave it out altogether.

I've also included an example image as the main product image.

Although I have chosen greyscale I would also like to see products with colour.

The product page is at https://kelvarn.global/collections/all
I add this so that you can chose any one of the titles for this template

Target Market(s)

This is aimed at professional footballers

Industry/Entity Type

Sporting Good

Font styles to use
Serif
Sans Serif

Colors

Designer to choose colors to be used in the design.

Requirements
Must have
• This must look like it is made for an affluent market.
• It may also be simple in its design but I do not wish to be too prescriptive with creativity.
• My typography is Montserrat
Nice to have
• Can include the colors of my logos:
• #5BA9DE
• #272B5F
• Or you can choose to go with greyscale
Should not have
• This is a product for serious athletes so it should look very professional and adult orientated (so not cartoonish its look)

```html
<!DOCTYPE html>
<html lang="en">
<head>
<meta charset="utf-8">
<title>Attacking Vision – Hypnosis Sessions</title>
<link rel="stylesheet" href="https://fonts.googleapis.com/css2?family=Montserrat:wght@300;500;600;800&display=swap">
<style>
  :root {
    --white: #ffffff;
    --sky: #17b6e0;
    --sky-mid: #139fcb;
    --ocean: #0f86ad;
    --deep: #0b3a4d;
    --deep-base: #0e4a5f;
    --navy: #272b5f;
    --brand-blue: #5ba9de;
    --gold: #b8ab6c;
    --photo-dark: #3b3a2c;
    --photo-mid: #8f8862;
    --photo-light: #d8d2a6;
  }
  * { margin: 0; padding: 0; box-sizing: border-box; }
  html, body { width: 1200px; height: 675px; overflow: hidden; background: var(--white); }
  .cover {
    position: relative;
    width: 1200px;
    height: 675px;
    overflow: hidden;
    font-family: "Montserrat", sans-serif;
  }
  .cover-art { position: absolute; inset: 0; width: 1200px; height: 675px; }
  .brand {
    position: absolute;
    left: 46px;
    top: 82px;
    width: 180px;
    text-align: center;
    color: var(--brand-blue);
    font-weight: 600;
    line-height: 1.35;
  }
  .brand-dot {
    display: block;
    width: 26px;
    height: 26px;
    margin: 0 auto 8px;
    border-radius: 50%;
    background: var(--brand-blue);
  }
  .brand-name { font-size: 9.5px; letter-spacing: 0.2px; }
  .brand-sub { font-size: 11.5px; letter-spacing: 1.5px; }
  .eyebrow {
    position: absolute;
    left: 119px;
    top: 229px;
    font-size: 19px;
    font-weight: 500;
    color: var(--navy);
  }
  .title {
    position: absolute;
    right: 494px;
    top: 288px;
    text-align: right;
    white-space: nowrap;
    color: var(--white);
    font-weight: 800;
    font-size: 112px;
    line-height: 0.82;
    letter-spacing: -3px;
    text-shadow: 4px 5px 8px rgba(0, 0, 0, 0.45);
  }
  .title span { display: block; }
  .benefit {
    position: absolute;
    left: 140px;
    top: 520px;
    display: flex;
    align-items: flex-start;
    gap: 17px;
  }
  .benefit-dot {
    flex: none;
    width: 29px;
    height: 29px;
    margin-top: 2px;
    border-radius: 50%;
    background: var(--gold);
  }
  .benefit-text {
    color: var(--white);
    font-weight: 300;
    font-size: 14.5px;
    line-height: 1.45;
    letter-spacing: 0.3px;
  }
</style>
</head>
<body>
<main class="cover">
  <svg class="cover-art" viewBox="0 0 1200 675" xmlns="http://www.w3.org/2000/svg">
    <defs>
      <linearGradient id="photo-tone" x1="0" y1="0" x2="0" y2="1">
        <stop offset="0" stop-color="var(--photo-dark)"/>
        <stop offset="0.45" stop-color="var(--photo-mid)"/>
        <stop offset="0.75" stop-color="var(--photo-light)"/>
        <stop offset="1" stop-color="var(--photo-mid)"/>
      </linearGradient>
    </defs>
    <path class="band-sky" d="M0 168 C250 150 520 90 700 0 L1200 0 L1200 675 L0 675 Z" fill="var(--sky)"/>
    <path class="band-sky-mid" d="M0 250 C250 235 480 205 640 150 L1200 150 L1200 675 L0 675 Z" fill="var(--sky-mid)"/>
    <path class="band-ocean" d="M0 330 C250 320 470 300 620 270 L1200 270 L1200 675 L0 675 Z" fill="var(--ocean)" opacity="0.55"/>
    <path class="band-deep" d="M0 405 C220 400 420 420 620 460 L1200 460 L1200 675 L0 675 Z" fill="var(--deep)"/>
    <rect class="band-base" x="0" y="633" width="1200" height="42" fill="var(--deep-base)"/>
    <path class="photo-frame-outer" d="M668 0 C600 110 575 250 590 380 C600 480 640 590 700 675 L1200 675 L1200 0 Z" fill="var(--ocean)"/>
    <path class="photo-frame-inner" d="M684 0 C616 110 592 250 606 380 C616 480 654 590 712 675 L1200 675 L1200 0 Z" fill="var(--sky)"/>
    <path class="hero-photo" role="img" aria-label="Two footballers leaping for the ball under stadium floodlights, warm sepia tone"
      d="M700 0 C634 110 610 250 622 380 C632 480 668 590 724 675 L1200 675 L1200 0 Z" fill="url(#photo-tone)"/>
  </svg>

  <div class="brand">
    <span class="brand-dot"></span>
    <div class="brand-name">ELIAS MARREN HYPNOTHERAPY</div>
    <div class="brand-sub">KELVARN</div>
  </div>

  <p class="eyebrow">Hypnosis sessions</p>

  <h1 class="title"><span>ATTACKING</span><span>VISION</span></h1>

  <div class="benefit">
    <span class="benefit-dot"></span>
    <p class="benefit-text">IMPROVE YOUR DECISION MAKING<br>WHEN YOU ARE ATTACKING.</p>
  </div>
</main>
</body>
</html>
```